Insurance Agency website design for Brellow Cover Insurance, LP

Build a website for Brellow Cover Insurance, LP which sells Homeowners, Auto, Renters, Condo, Flood, Disability, Life, Umbrella, and health insurance. We need the coolest insurance agency website out there to get quotes, contact us, or get additional information. Please list the following insurance companies we work with: Varnix, Ostle, Meridale Mutual, Quillor, Dunmarrow, KGZ, and Pellwick.

Make a design similar to https://www.fernagentry.com/

Selling personal insurance policies

```html
<!DOCTYPE html>
<html lang="en">
<head>
<meta charset="utf-8">
<title>Brellow Cover Insurance</title>
<link rel="stylesheet" href="https://fonts.googleapis.com/css2?family=Lexend:wght@300;400;500;600;700&display=swap">
<style>
:root{
  --navy:#0b2277;
  --navy-deep:#0a1f6b;
  --green:#3f9314;
  --ink:#222;
  --muted:#333;
  --sky:#dce7fb;
  --mint:#dcefe3;
  --white:#fff;
  --black:#000;
}
*{box-sizing:border-box;margin:0;padding:0}
html,body{width:1200px;height:3426px;overflow:hidden}
body{font-family:"Lexend",sans-serif;color:var(--ink);background:var(--white);position:relative}
.abs{position:absolute}
a{color:inherit;text-decoration:none}
.btn{position:absolute;display:flex;align-items:center;justify-content:center;gap:12px;background:var(--navy);color:var(--white);font-size:15px;letter-spacing:.5px;border-radius:3px;height:42px}
.btn.green{background:var(--green)}
.arrow-ne{width:11px;height:11px}

/* hero */
.hero{position:absolute;left:0;top:0;width:1200px;height:630px;background:linear-gradient(90deg,#f1f4f8 0%,#e6ecf3 45%,#d8e0ea 100%)}
.hero-photo{position:absolute;left:540px;top:120px;width:660px;height:510px;background:linear-gradient(135deg,#d6dde6 0%,#b8c2cf 45%,#6e7887 75%,#2f3441 100%);-webkit-mask:linear-gradient(90deg,transparent 0,#000 22%);mask:linear-gradient(90deg,transparent 0,#000 22%)}
.topbar{position:absolute;top:10px;left:142px;width:917px;height:22px;display:flex;justify-content:space-between;align-items:center;font-size:13px}
.socials{display:flex;gap:7px}
.socials span{width:19px;height:19px;border:1px solid #555;border-radius:50%}
.contact-top{display:flex;gap:16px;align-items:center}
.contact-top i{display:inline-block;width:19px;height:19px;border:1px solid #555;border-radius:50%;vertical-align:middle;margin-right:7px;font-style:normal}
.navbar{position:absolute;top:52px;left:142px;width:917px;height:43px;display:flex;align-items:center;justify-content:space-between}
.brand{font-size:21px;font-weight:600;color:#111;letter-spacing:.2px}
.menu{display:flex;align-items:center;gap:30px;font-size:13px;color:#111}
.menu .btn{position:static;height:43px;padding:0 17px;font-size:15px}
.hero h1{position:absolute;left:142px;top:218px;font-size:52px;line-height:59px;font-weight:700;color:#2a2a2a;letter-spacing:.5px}
.hero p{position:absolute;left:142px;top:342px;font-size:16px;line-height:28px;color:#222}

/* features */
.feature{position:absolute;top:716px;width:219px;height:211px;color:var(--white);text-align:center;font-size:17px;line-height:21px;font-weight:300}
.feature.blue{background:var(--navy-deep)}
.feature.grn{background:var(--green)}
.feature .ic{width:84px;height:84px;border-radius:50%;background:var(--white);margin:40px auto 12px;display:flex;align-items:center;justify-content:center;box-shadow:0 0 0 3px rgba(255,255,255,.35)}

/* about */
.about-bg{position:absolute;left:141px;top:1016px;width:374px;height:507px;background:var(--mint)}
.about-photo{position:absolute;left:200px;top:1088px;width:375px;height:352px;background:linear-gradient(135deg,#8e9696 0%,#cbc6bd 45%,#e8e6e1 70%,#a9a49c 100%)}
.badge{position:absolute;left:423px;top:1292px;width:180px;height:118px;background:var(--green);border:4px solid var(--white);border-radius:8px;color:var(--white);text-align:center}
.badge b{display:block;font-size:42px;font-weight:600;margin-top:8px;line-height:46px}
.badge span{font-size:16px;font-weight:300;line-height:22px}
.about-text{position:absolute;left:644px;top:1066px;width:410px}
.about-text h2{font-size:27px;font-weight:600;color:#222;margin-bottom:20px}
.about-text p{font-size:14.5px;line-height:21.3px;color:#333;margin-bottom:7px;font-weight:300}

/* types */
.types{position:absolute;left:0;top:1609px;width:1200px;height:765px;background:var(--sky)}
.types-text{position:absolute;left:142px;top:1822px;width:415px}
.types-text h2{font-size:28px;font-weight:600;color:#111;margin-bottom:12px}
.types-text p{font-size:14.5px;line-height:21.3px;color:#333;margin-bottom:10px;font-weight:300}
.tcard{position:absolute;width:212px;height:241px;color:var(--white);text-align:center}
.tcard.blue{background:var(--navy-deep)}
.tcard.grn{background:var(--green)}
.tcard .ic{width:86px;height:86px;border-radius:50%;background:var(--white);margin:27px auto 10px;display:flex;align-items:center;justify-content:center;box-shadow:0 0 0 6px rgba(255,255,255,.3)}
.tcard h3{font-size:15px;font-weight:600;letter-spacing:.3px;margin-bottom:4px}
.tcard p{font-size:11.5px;line-height:17px;font-weight:300;padding:0 16px}
.tcard .go{position:absolute;left:88px;bottom:-17px;width:34px;height:34px;display:flex;align-items:center;justify-content:center;border-radius:2px}
.tcard.blue .go{background:var(--green)}
.tcard.grn .go{background:var(--navy-deep)}

/* partners */
.partners h2{position:absolute;left:0;top:2456px;width:1200px;text-align:center;font-size:28px;font-weight:600;color:#111}
.plogo{position:absolute;top:2520px;width:160px;height:97px;background:var(--white);box-shadow:0 2px 10px rgba(0,0,0,.12);display:flex;align-items:center;justify-content:center;font-size:19px;font-weight:500;color:#1c2a3a}
.pnav{position:absolute;top:2548px;width:42px;height:42px;border-radius:50%;display:flex;align-items:center;justify-content:center}
.pnav.prev{left:141px;background:var(--white);box-shadow:0 2px 8px rgba(0,0,0,.2)}
.pnav.next{left:1016px;background:var(--navy-deep)}

/* cta */
.cta{position:absolute;left:0;top:2708px;width:1200px;height:303px;background:linear-gradient(90deg,#1b3a93 0%,#243f95 40%,#1d3887 100%);color:var(--white);text-align:center}
.cta h2{margin-top:58px;font-size:28px;font-weight:600}
.cta p{width:540px;margin:10px auto 0;font-size:15px;line-height:21.5px;font-weight:300}
.cta .btn{left:522px;top:198px;width:155px}

/* footer */
.footer{position:absolute;left:0;top:3011px;width:1200px;height:374px;background:var(--black);color:var(--white)}
.footer h4{font-size:16px;font-weight:400;position:relative;padding-bottom:12px}
.footer h4:after{content:"";position:absolute;left:0;bottom:0;width:30px;height:2px;background:var(--white)}
.fcol{position:absolute;top:104px;font-size:13px;font-weight:300}
.fcol ul{list-style:none;margin-top:20px}
.fcol li{margin-bottom:11px;display:flex;align-items:center;gap:8px}
.fsoc li{margin-bottom:11px}
.fsoc i{width:28px;height:28px;border:1px solid var(--white);border-radius:50%;display:inline-block}
.fcontact li{align-items:flex-start;line-height:19px;margin-bottom:13px}
.copyright{position:absolute;left:0;top:3385px;width:1200px;height:41px;background:var(--navy-deep);color:var(--white);font-size:11.5px;font-weight:300;display:flex;align-items:center;justify-content:center}
</style>
</head>
<body>

<!-- Hero -->
<section class="hero">
  <div class="hero-photo" role="img" aria-label="Business people shaking hands across a meeting table"></div>
  <div class="topbar">
    <div class="socials"><span></span><span></span><span></span><span></span></div>
    <div class="contact-top">
      <span><i></i>(555) 318-2740</span>
      <span><i></i>info@BrellowCover.com</span>
    </div>
  </div>
  <nav class="navbar">
    <div class="brand">BRELLOW COVER INSURANCE</div>
    <div class="menu">
      <a href="#">Home</a><a href="#">About Us</a>
      <a href="#">Insurance Types &#8964;</a><a href="#">Contact Us</a>
      <a class="btn" href="#">Get a Quote</a>
    </div>
  </nav>
  <h1>PROTECT WHAT<br>MATTERS MOST</h1>
  <p>Comprehensive insurance solutions for your<br>home, vehicle, health, and loved ones</p>
  <a class="btn" href="#" style="left:141px;top:411px;width:127px">Get a Quote</a>
</section>

<!-- Features -->
<div class="feature blue" style="left:142px"><div class="ic"><svg width="40" height="40" viewBox="0 0 40 40" fill="none" stroke="#0b2277" stroke-width="1.6"><rect x="9" y="6" width="20" height="27"/><path d="M13 13h12M13 18h12M13 23h8"/><circle cx="29" cy="29" r="5"/></svg></div>Insurance<br>Policies</div>
<div class="feature grn" style="left:375px"><div class="ic"><svg width="46" height="46" viewBox="0 0 46 46" fill="none" stroke="#0b2277" stroke-width="1.8"><circle cx="23" cy="23" r="19"/><circle cx="16" cy="19" r="1.5"/><circle cx="30" cy="19" r="1.5"/><path d="M14 27c4 6 14 6 18 0"/></svg></div>1000+ Happy<br>Clients</div>
<div class="feature blue" style="left:607px"><div class="ic"><svg width="42" height="42" viewBox="0 0 42 42" fill="none" stroke="#0b2277" stroke-width="1.6"><circle cx="21" cy="16" r="8"/><path d="M8 36c2-8 24-8 26 0M12 16a9 9 0 0 1 18 0"/></svg></div>Professional<br>Support</div>
<div class="feature grn" style="left:840px"><div class="ic"><svg width="46" height="46" viewBox="0 0 46 46" fill="none" stroke="#0b2277" stroke-width="1.6"><circle cx="23" cy="23" r="9"/><circle cx="23" cy="23" r="17" stroke-dasharray="6 4"/></svg></div>Free Lifetime<br>Updates</div>

<!-- About -->
<div class="about-bg"></div>
<svg class="abs" style="left:186px;top:1088px" width="390" height="370" fill="none" stroke="#0b1f9a" stroke-width="6"><path d="M3 0V365H330M340 365H390"/></svg>
<div class="about-photo" role="img" aria-label="Advisor meeting with a senior couple at a table"></div>
<div class="badge"><b>50+</b><span>Skilled<br>Professionals</span></div>
<div class="about-text">
  <h2>BRELLOW COVER INSURANCE</h2>
  <p>Brellow Cover Insurance is a full-service, independent insurance agency with over three decades of experience in delivering comprehensive insurance solutions to individuals.</p>
  <p>We proudly offer a diverse portfolio of products from more than 20 of the most reputable and financially secure companies in the industry. Our dedicated team of over 50 skilled professionals is committed to customizing these products and services to meet the unique needs of each client.</p>
  <p>At Brellow Cover Insurance, our experts are focused on addressing the individual needs of our clients, ensuring exceptional service and support at every step.</p>
</div>
<a class="btn" href="#" style="left:644px;top:1427px;width:134px">Read More <svg class="arrow-ne" viewBox="0 0 10 10" stroke="#fff" stroke-width="1.3" fill="none"><path d="M1 9 9 1M3 1h6v6"/></svg></a>

<!-- Insurance types -->
<section class="types"></section>
<div class="types-text">
  <h2>INSURANCE TYPES</h2>
  <p>Lorem ipsum dolor sit amet, consectetuer adipiscing elit, sed diam nonummy nibh euismod tincidunt ut laoreet dolore magna aliquam erat volutpat.</p>
  <p>Lorem ipsum dolor sit amet, consectetuer adipiscing elit, sed diam nonummy nibh euismod tincidunt ut laoreet dolore magna aliquam erat volutpat. Ut wisi enim ad minim veniam, quis nostrud exerci tation ullamcorper suscipit lobortis nisl ut aliquip ex ea commodo consequat. Duis autem vel eum iriure dolor in hendrerit in vulputate velit esse molestie consequat.</p>
</div>
<a class="btn" href="#" style="left:142px;top:2114px;width:198px">View All Insurance <svg class="arrow-ne" viewBox="0 0 10 10" stroke="#fff" stroke-width="1.3" fill="none"><path d="M1 9 9 1M3 1h6v6"/></svg></a>

<div class="tcard blue" style="left:612px;top:1699px"><div class="ic"><svg width="44" height="44" viewBox="0 0 44 44" fill="none" stroke="#0b2277" stroke-width="1.6"><path d="M6 22 22 8l16 14M11 18v18h22V18"/><circle cx="22" cy="26" r="5"/></svg></div><h3>HOMEOWNERS</h3><p>Lorem Ipsum is simply dummy text of the printing typesetting industry Lorem Ipsum has</p><span class="go"><svg class="arrow-ne" viewBox="0 0 10 10" stroke="#fff" stroke-width="1.3" fill="none"><path d="M1 9 9 1M3 1h6v6"/></svg></span></div>
<div class="tcard grn" style="left:847px;top:1748px"><div class="ic"><svg width="46" height="40" viewBox="0 0 46 40" fill="none" stroke="#0b2277" stroke-width="1.6"><path d="M4 26v-8l5-8h18l5 8v8zM4 26v5h6v-5M26 26v5h6v-5"/><path d="M34 8l8 3v7c0 5-4 8-8 9-4-1-8-4-8-9v-7z"/></svg></div><h3>AUTO</h3><p>Lorem Ipsum is simply dummy text of the printing typesetting industry Lorem Ipsum has</p><span class="go"><svg class="arrow-ne" viewBox="0 0 10 10" stroke="#fff" stroke-width="1.3" fill="none"><path d="M1 9 9 1M3 1h6v6"/></svg></span></div>
<div class="tcard grn" style="left:612px;top:1980px"><div class="ic"><svg width="44" height="44" viewBox="0 0 44 44" fill="none" stroke="#0b2277" stroke-width="1.6"><path d="M6 22 22 8l16 14M11 18v18h22V18"/><path d="M22 22v10M17 28l5 4 5-4"/></svg></div><h3>RENTERS</h3><p>Lorem Ipsum is simply dummy text of the printing typesetting industry Lorem Ipsum has</p><span class="go"><svg class="arrow-ne" viewBox="0 0 10 10" stroke="#fff" stroke-width="1.3" fill="none"><path d="M1 9 9 1M3 1h6v6"/></svg></span></div>
<div class="tcard blue" style="left:847px;top:2030px"><div class="ic"><svg width="40" height="44" viewBox="0 0 40 44" fill="none" stroke="#0b2277" stroke-width="1.8"><circle cx="18" cy="6" r="3"/><path d="M18 11v12h10l4 10M14 17a11 11 0 1 0 12 18"/></svg></div><h3>DISABILITY</h3><p>Lorem Ipsum is simply dummy text of the printing typesetting industry Lorem Ipsum has</p><span class="go"><svg class="arrow-ne" viewBox="0 0 10 10" stroke="#fff" stroke-width="1.3" fill="none"><path d="M1 9 9 1M3 1h6v6"/></svg></span></div>

<!-- Partners -->
<section class="partners">
  <h2>OUR PARTNERS</h2>
  <span class="pnav prev"><svg width="14" height="12" viewBox="0 0 14 12" stroke="#111" stroke-width="1.8" fill="none"><path d="M13 6H2M6 1 1 6l5 5"/></svg></span>
  <div class="plogo" style="left:245px">Varnix</div>
  <div class="plogo" style="left:428px">Ostle</div>
  <div class="plogo" style="left:611px">Meridale Mutual</div>
  <div class="plogo" style="left:795px">Dunmarrow</div>
  <span class="pnav next"><svg width="14" height="12" viewBox="0 0 14 12" stroke="#fff" stroke-width="1.8" fill="none"><path d="M1 6h11M8 1l5 5-5 5"/></svg></span>
</section>

<!-- CTA -->
<section class="cta" role="img" aria-label="Smiling clients behind a blue overlay">
  <h2>GET A QUOTE TODAY</h2>
  <p>Lorem ipsum dolor sit amet, consectetuer adipiscing elit, sed diam nonummy nibh euismod tincidunt ut laoreet dolore magna aliquam erat volutpat. Ut wisi enim ad minim veniam.</p>
  <a class="btn green" href="#">Get a Quote <svg class="arrow-ne" viewBox="0 0 10 10" stroke="#fff" stroke-width="1.3" fill="none"><path d="M1 9 9 1M3 1h6v6"/></svg></a>
</section>

<!-- Footer -->
<footer class="footer">
  <div class="fcol" style="left:142px;top:102px;width:320px">
    <div style="font-size:21px;font-weight:600;margin-bottom:26px">BRELLOW COVER INSURANCE</div>
    <p style="line-height:21px">Lorem ipsum dolor sit amet, consectetuer adipiscing elit, sed diam nonummy nibh euismod tincidunt utted is laoreet dolore magna aliquam erat volutpat. Ut wisi enim ad minim veniam.<br><u>Read More</u></p>
  </div>
  <div class="fcol" style="left:512px">
    <h4>Quick Links</h4>
    <ul><li>&raquo; Home</li><li>&raquo; About Us</li><li>&raquo; Insurance Types</li><li>&raquo; Contact Us</li><li>&raquo; Get a Quote</li></ul>
  </div>
  <div class="fcol fsoc" style="left:690px">
    <h4>Follow Us</h4>
    <ul><li><i></i>Chatterly</li><li><i></i>Streamly</li><li><i></i>Snapnest</li><li><i></i>Chirpline</li></ul>
  </div>
  <div class="fcol fcontact" style="left:829px;width:240px">
    <h4>Contact Details</h4>
    <ul>
      <li><svg width="12" height="16" viewBox="0 0 12 16"><path d="M6 0a6 6 0 0 0-6 6c0 4 6 10 6 10s6-6 6-10a6 6 0 0 0-6-6zm0 8a2 2 0 1 1 0-4 2 2 0 0 1 0 4z" fill="#fff"/></svg><span>Address<br>123 Building Name,<br>City Name, State XY-123456.</span></li>
      <li><svg width="13" height="13" viewBox="0 0 13 13"><path d="M3 0 5 3 3.5 4.5a8 8 0 0 0 5 5L10 8l3 2-1 3C6 13 0 7 0 1z" fill="#fff"/></svg><span>Phone<br>(555) 318-2740</span></li>
      <li><svg width="14" height="11" viewBox="0 0 14 11"><rect width="14" height="11" fill="#fff"/><path d="M0 0l7 6 7-6" stroke="#000" fill="none"/></svg><span>Email<br>info@BrellowCover.com</span></li>
    </ul>
  </div>
</footer>
<div class="copyright">Copyright © 2025 Brellow Cover Insurance. All Rights Reserved.</div>

</body>
</html>
```